Business Card for Vorla Parts Wholesale supplier

Hi There! I need a new business card for our company. We are specialized in selling Vorla parts, mostly we sell new LCD screens for Zelnar and Drelks. I would like to see that back in the design.

You can find the colors and logo's on our website: www.hartuvo.nl

Industry/Entity Type

Business

Contact Information for Business Card

My Details:
Tobias Lindqvist

Phone: 0031687203316
E-mail: Tobias@hartuvo.nl

Slogan: "Because Every Part Counts"

Font styles to use
Sans Serif

Colors

Designer to choose colors to be used in the design.

Requirements
Must have
• A Black backside with the Hartuvo logo on it. The front side should be clean with only my contact details.
• But I'm also open for something really different or awesome!
Nice to have
• Remember that we are in the parts & repairing industry, So i'll be handing those business cards mainly to repair companies. Maybe you can do something with that thought :)

```html
<!DOCTYPE html>
<html lang="en">
<head>
<meta charset="utf-8">
<title>Hartuvo Business Card</title>
<link rel="stylesheet" href="https://fonts.googleapis.com/css2?family=Montserrat:wght@400;700;800&display=swap">
<style>
  :root {
    --page-bg: #d9d6d1;
    --card-black: #0b0b0b;
    --accent-orange: #f06a1d;
    --text-white: #f2f2f2;
    --text-grey: #d0d0d0;
  }
  * { box-sizing: border-box; margin: 0; padding: 0; }
  html, body {
    width: 1200px;
    height: 950px;
    overflow: hidden;
    background: var(--page-bg);
    font-family: "Montserrat", Arial, sans-serif;
  }
  .card-set {
    position: relative;
    width: 1200px;
    height: 950px;
  }
  .card {
    position: absolute;
    top: 135px;
    width: 400px;
    height: 680px;
    background: linear-gradient(160deg, #1e1e1e 0%, var(--card-black) 45%, var(--card-black) 100%);
    border-radius: 4px;
    box-shadow: 0 12px 30px rgba(0,0,0,0.35);
    overflow: hidden;
  }
  .card--front { left: 140px; }
  .card--back { left: 660px; }
  .card-frame {
    position: absolute;
    inset: 0;
    width: 400px;
    height: 680px;
  }
  .card-frame polygon {
    fill: none;
    stroke: var(--accent-orange);
    stroke-width: 1.6;
  }

  /* Front */
  .brand {
    position: absolute;
    top: 78px;
    left: 0;
    right: 0;
    display: flex;
    align-items: center;
    justify-content: center;
    gap: 14px;
  }
  .brand-dot {
    width: 34px;
    height: 34px;
    border-radius: 50%;
    background: var(--accent-orange);
  }
  .brand-name {
    font-weight: 800;
    font-size: 46px;
    color: var(--text-white);
    letter-spacing: 1px;
    line-height: 1;
  }
  .contact-list {
    position: absolute;
    top: 200px;
    left: 0;
    right: 0;
    display: flex;
    flex-direction: column;
    align-items: center;
    text-align: center;
  }
  .contact-item {
    display: flex;
    flex-direction: column;
    align-items: center;
    margin-bottom: 22px;
  }
  .contact-icon {
    width: 26px;
    height: 26px;
    margin-bottom: 8px;
  }
  .contact-icon .octagon { fill: var(--accent-orange); }
  .contact-icon .glyph { fill: #ffffff; }
  .contact-icon .glyph-line { fill: none; stroke: #ffffff; stroke-width: 1.6; }
  .contact-icon .glyph-line--orange { stroke: var(--accent-orange); }
  .contact-name {
    font-weight: 700;
    font-size: 26px;
    color: var(--accent-orange);
    letter-spacing: 1px;
  }
  .contact-text {
    font-weight: 400;
    font-size: 19px;
    color: var(--text-grey);
    letter-spacing: 1px;
  }

  /* Back */
  .back-brand {
    position: absolute;
    top: 255px;
    left: 0;
    right: 0;
    display: flex;
    align-items: center;
    justify-content: center;
    gap: 14px;
  }
  .back-brand .brand-dot { width: 40px; height: 40px; }
  .back-brand .brand-name {
    font-size: 52px;
    color: var(--accent-orange);
  }
  .slogan {
    position: absolute;
    top: 400px;
    left: 0;
    right: 0;
    text-align: center;
    font-weight: 700;
    font-size: 21px;
    color: var(--text-white);
  }
</style>
</head>
<body>
<main class="card-set">

  <section class="card card--front" aria-label="Business card front">
    <svg class="card-frame" viewBox="0 0 400 680" aria-hidden="true">
      <polygon points="38,18 362,18 382,38 382,642 362,662 38,662 18,642 18,38"/>
    </svg>

    <div class="brand">
      <span class="brand-dot"></span>
      <span class="brand-name">hartuvo</span>
    </div>

    <div class="contact-list">
      <div class="contact-item">
        <svg class="contact-icon" viewBox="0 0 26 26" aria-hidden="true">
          <polygon class="octagon" points="8,1 18,1 25,8 25,18 18,25 8,25 1,18 1,8"/>
          <circle class="glyph" cx="13" cy="10" r="3.5"/>
          <path class="glyph" d="M6.5 20 Q13 12 19.5 20 Z"/>
        </svg>
        <span class="contact-name">Tobias Lindqvist</span>
      </div>

      <div class="contact-item">
        <svg class="contact-icon" viewBox="0 0 26 26" aria-hidden="true">
          <polygon class="octagon" points="8,1 18,1 25,8 25,18 18,25 8,25 1,18 1,8"/>
          <path class="glyph" d="M8 7 L11 7 L12 10.5 L10.5 12 Q12 15 14 15.5 L15.5 14 L19 15 L19 18 Q16 20 12 16.5 Q8 13 8 7 Z"/>
        </svg>
        <span class="contact-text">0031687203316</span>
      </div>

      <div class="contact-item">
        <svg class="contact-icon" viewBox="0 0 26 26" aria-hidden="true">
          <polygon class="octagon" points="8,1 18,1 25,8 25,18 18,25 8,25 1,18 1,8"/>
          <rect class="glyph" x="6.5" y="8.5" width="13" height="9" rx="1"/>
          <polyline class="glyph-line glyph-line--orange" points="6.5,9 13,14 19.5,9"/>
        </svg>
        <span class="contact-text">Tobias@hartuvo.nl</span>
      </div>

      <div class="contact-item">
        <svg class="contact-icon" viewBox="0 0 26 26" aria-hidden="true">
          <polygon class="octagon" points="8,1 18,1 25,8 25,18 18,25 8,25 1,18 1,8"/>
          <circle class="glyph-line" cx="13" cy="13" r="6"/>
          <ellipse class="glyph-line" cx="13" cy="13" rx="2.6" ry="6"/>
          <line class="glyph-line" x1="7" y1="13" x2="19" y2="13"/>
        </svg>
        <span class="contact-text">www.hartuvo.nl</span>
      </div>
    </div>
  </section>

  <section class="card card--back" aria-label="Business card back">
    <svg class="card-frame" viewBox="0 0 400 680" aria-hidden="true">
      <polygon points="38,18 362,18 382,38 382,642 362,662 38,662 18,642 18,38"/>
    </svg>

    <div class="back-brand">
      <span class="brand-dot"></span>
      <span class="brand-name">hartuvo</span>
    </div>

    <p class="slogan">Because Every Part Counts</p>
  </section>

</main>
</body>
</html>
```